Design a modern, classy & professional business card for an online real estate agency, specializing in medium-luxury properties in Thailand and later in Singapore and UK.

Possible design ideas so far: (not essential)

- curved corner(s) to the card, white on front & turquoise on back or visa versa.

- front of card - clear and simple, company name in metallic grey/monochrome, logo graphic & company name on front in spot UV or embossed/debossed effect.

- back of card - large, close-cropped, 'ghost' patterns of the C-shaped curves of logo, or company name repeated on back of card in spot UV.

Target Market(s)

- young to middle-aged professionals mainly (but ideally should design should suit all)

- UK, US,EU,AUS & ASIAN mainly (but ideally should design should suit all countries)

Industry/Entity Type

Real Estate

Requirements
Must have
• THEME:
- Luxurious & Modern
- Clean & striking
- Unique & creative

INFO:
- Logo & company name on front
- Contact details on back:

Tobias Hennlund
Managing Director

www.velmontestates.asia
www.velmontestates.co.uk

Tel: 083-274-6159
email: tobias@velmontestates.asia

(contact details can be displayed in any order as suites design.)

Nice to have
• - curved corner(s) to the card, white on front & turquoise on back or visa versa.

Should not have
• - No generic images of properties, palm trees/coconut trees etc.

- No other other bold colors, except for main turquoise, grey, metallic white & black theme.

- No obvious business card templates

```html
<!DOCTYPE html>
<html lang="en">
<head>
<meta charset="utf-8">
<title>Velmont Estates Business Card</title>
<link rel="stylesheet" href="https://fonts.googleapis.com/css2?family=Marcellus&family=Exo+2:wght@400;600;700&display=swap">
<style>
  :root {
    --backdrop: #e6e4df;
    --card: #fbfbfb;
    --card-edge: #e9e9e9;
    --turquoise: #25c2c0;
    --grey-band: #8e9093;
    --brand-grey: #75777a;
    --ink: #2b2c2e;
    --ink-soft: #55575a;
  }
  * { box-sizing: border-box; margin: 0; padding: 0; }
  html, body {
    width: 1057px;
    height: 1200px;
    overflow: hidden;
    background: var(--backdrop);
  }
  .canvas {
    position: relative;
    width: 1057px;
    height: 1200px;
    display: flex;
    align-items: center;
    justify-content: center;
    gap: 80px;
  }
  .card {
    position: relative;
    width: 420px;
    height: 720px;
    background: linear-gradient(160deg, #ffffff 0%, var(--card) 55%, var(--card-edge) 100%);
    border-radius: 6px;
    box-shadow: 0 14px 30px rgba(0,0,0,0.18);
    overflow: hidden;
  }

  /* brand lockup */
  .brand {
    position: absolute;
    left: 0;
    right: 0;
    display: flex;
    flex-direction: column;
    align-items: center;
    font-family: "Marcellus", serif;
    color: var(--brand-grey);
  }
  .brand-mark {
    background: var(--turquoise);
    margin-bottom: 12px;
  }
  .brand-name { line-height: 1; }
  .brand-sub { letter-spacing: 0.28em; margin-top: 4px; line-height: 1; }

  .card-back .brand { top: 48px; }
  .card-back .brand-mark { width: 66px; height: 66px; }
  .card-back .brand-name { font-size: 40px; }
  .card-back .brand-sub { font-size: 14px; }

  .card-front .brand { top: 262px; }
  .card-front .brand-mark { width: 80px; height: 80px; margin-bottom: 14px; }
  .card-front .brand-name { font-size: 48px; }
  .card-front .brand-sub { font-size: 17px; }

  /* side stripe */
  .stripe-grey {
    position: absolute;
    right: 26px;
    top: 0;
    width: 24px;
    height: 300px;
    background: var(--grey-band);
  }
  .stripe-turquoise {
    position: absolute;
    right: 26px;
    top: 300px;
    width: 24px;
    bottom: 0;
    background: var(--turquoise);
  }
  .stripe-icon {
    position: absolute;
    right: 30px;
    width: 16px;
    height: 16px;
  }

  /* contact block */
  .contact {
    position: absolute;
    right: 66px;
    text-align: right;
    font-family: "Exo 2", sans-serif;
    color: var(--ink-soft);
  }
  .person-name {
    top: 300px;
    font-size: 24px;
    font-weight: 600;
    letter-spacing: 0.04em;
    color: var(--turquoise);
    text-transform: uppercase;
    line-height: 1;
  }
  .person-role {
    top: 330px;
    font-size: 12px;
    letter-spacing: 0.08em;
    color: var(--turquoise);
    text-transform: uppercase;
  }
  .contact-line { font-size: 15px; letter-spacing: 0.03em; }
  .line-phone { top: 370px; }
  .line-mobile { top: 410px; }
  .line-email { top: 450px; }
  .line-web { top: 490px; }
  .address {
    top: 572px;
    font-size: 19px;
    font-weight: 600;
    line-height: 1.4;
    color: var(--ink);
  }
</style>
</head>
<body>
<main class="canvas">

  <section class="card card-back" aria-label="Card back with contact details">
    <div class="brand">
      <div class="brand-mark"></div>
      <div class="brand-name">Velmont</div>
      <div class="brand-sub">ESTATES</div>
    </div>

    <div class="stripe-grey"></div>
    <div class="stripe-turquoise"></div>

    <svg class="stripe-icon" style="top:372px" viewBox="0 0 16 16" aria-hidden="true">
      <path d="M4 1.5 6 4.5 4.8 6.2c.9 1.9 2.3 3.3 4.2 4.2l1.6-1.2 3 2-1.2 2.8C7 14 2 9 1.2 3z" fill="#fff"/>
    </svg>
    <svg class="stripe-icon" style="top:412px" viewBox="0 0 16 16" aria-hidden="true">
      <rect x="4" y="1" width="8" height="14" rx="1.5" fill="#fff"/>
      <rect x="5.5" y="3" width="5" height="8" fill="#25c2c0"/>
    </svg>
    <svg class="stripe-icon" style="top:452px" viewBox="0 0 16 16" aria-hidden="true">
      <rect x="1" y="3" width="14" height="10" rx="1" fill="#fff"/>
      <path d="M1.5 3.8 8 9l6.5-5.2" fill="none" stroke="#25c2c0" stroke-width="1.3"/>
    </svg>
    <svg class="stripe-icon" style="top:492px" viewBox="0 0 16 16" aria-hidden="true">
      <circle cx="8" cy="8" r="6.5" fill="#fff"/>
      <path d="M1.5 8h13M8 1.5c-3 3.5-3 9.5 0 13M8 1.5c3 3.5 3 9.5 0 13" fill="none" stroke="#25c2c0" stroke-width="1"/>
    </svg>

    <div class="contact person-name">Tobias Hennlund</div>
    <div class="contact person-role">Managing Director</div>
    <div class="contact contact-line line-phone">083-274-6159</div>
    <div class="contact contact-line line-mobile">www.velmontestates.co.uk</div>
    <div class="contact contact-line line-email">tobias@velmontestates.asia</div>
    <div class="contact contact-line line-web">www.velmontestates.asia</div>
    <div class="contact address">27 Larkspur Road,<br>3rd Floor Suite 4</div>
  </section>

  <section class="card card-front" aria-label="Card front with company name">
    <div class="brand">
      <div class="brand-mark"></div>
      <div class="brand-name">Velmont</div>
      <div class="brand-sub">ESTATES</div>
    </div>
  </section>

</main>
</body>
</html>
```